Investment company needing business card

We are wanting a business card which looks sharp and easy on the eye. We are thinking of having a business card with the logo embossed on it, to really make it stand out. We will only have a small amount of information of the business card, person's name, position, email address and phone number

Contact Information for Business Card

Danielle Frost
Executive Assistant
+64 21 473 5162
danielf@harwickpartners.co.nz

Requirements
Must have
• Embossed logo
Should not have
• Not to be busy

```html
<!DOCTYPE html>
<html lang="en">
<head>
<meta charset="utf-8">
<title>Harwick Partners – Business Card</title>
<link href="https://fonts.googleapis.com/css2?family=Lato:wght@400;700;900&display=swap" rel="stylesheet">
<style>
  :root {
    --backdrop: #666666;
    --card-white: #ffffff;
    --brand-green: #1fb56e;
    --brand-green-bright: #1ec677;
    --back-green: #27b573;
    --ink: #333333;
    --rule: #b5b5b5;
  }
  * { margin: 0; padding: 0; box-sizing: border-box; }
  html, body {
    width: 1200px;
    height: 802px;
    overflow: hidden;
    background: var(--backdrop);
    font-family: "Lato", sans-serif;
  }
  .canvas {
    position: relative;
    width: 1200px;
    height: 802px;
  }
  .card {
    position: absolute;
    top: 274px;
    width: 443px;
    height: 265px;
  }
  .card--front { left: 136px; background: var(--card-white); }
  .card--back  { left: 624px; background: var(--back-green); }

  /* Front */
  .brand {
    position: absolute;
    right: 27px;
    top: 70px;
    display: flex;
    align-items: center;
    gap: 8px;
  }
  .brand__mark {
    width: 22px;
    height: 22px;
    background: var(--brand-green);
  }
  .brand__name {
    font-weight: 900;
    font-size: 22px;
    letter-spacing: 0.5px;
    color: var(--brand-green);
    white-space: nowrap;
  }
  .person {
    position: absolute;
    left: 28px;
    right: 27px;
    top: 155px;
  }
  .person__name {
    font-weight: 900;
    font-size: 18px;
    color: var(--brand-green);
    letter-spacing: 0.2px;
    line-height: 1.1;
  }
  .person__role-row {
    display: flex;
    align-items: center;
    gap: 6px;
    margin-top: 1px;
  }
  .person__role {
    font-size: 13px;
    color: var(--ink);
    white-space: nowrap;
  }
  .person__rule {
    flex: 1;
    height: 1px;
    background: var(--rule);
  }
  .contact {
    position: absolute;
    right: 27px;
    top: 203px;
    list-style: none;
    text-align: right;
    font-size: 13px;
    color: var(--ink);
    line-height: 17px;
  }
  .contact__item {
    display: flex;
    justify-content: flex-end;
    align-items: center;
    gap: 3px;
  }
  .contact__icon { width: 10px; height: 10px; fill: var(--brand-green-bright); }

  /* Back */
  .back-brand {
    position: absolute;
    inset: 0;
    display: flex;
    align-items: center;
    justify-content: center;
    gap: 12px;
  }
  .back-brand__mark {
    width: 26px;
    height: 26px;
    background: #ffffff;
  }
  .back-brand__name {
    font-weight: 900;
    font-size: 30px;
    letter-spacing: 0.5px;
    color: #ffffff;
    white-space: nowrap;
  }
</style>
</head>
<body>
<main class="canvas">
  <section class="card card--front" aria-label="Business card front">
    <div class="brand">
      <span class="brand__mark"></span>
      <span class="brand__name">HARWICK PARTNERS</span>
    </div>
    <div class="person">
      <h1 class="person__name">DANIELLE FROST</h1>
      <div class="person__role-row">
        <span class="person__role">Executive Assistant</span>
        <span class="person__rule"></span>
      </div>
    </div>
    <ul class="contact">
      <li class="contact__item">+64 21 473 5162
        <svg class="contact__icon" viewBox="0 0 10 10" aria-hidden="true"><path d="M1 3.5C1 2 2.5 1.5 5 1.5S9 2 9 3.5L7.5 4 7 3H3L2.5 4ZM2.5 4.5 3.5 3.8h3l1 .7V8.5h-5Z"/></svg>
      </li>
      <li class="contact__item">danielf@harwickpartners.co.nz
        <svg class="contact__icon" viewBox="0 0 10 10" aria-hidden="true"><path d="M1 2h8v6H1Z M1.6 2.6 5 5.4 8.4 2.6" stroke="#fff" stroke-width="0.7"/></svg>
      </li>
    </ul>
  </section>

  <section class="card card--back" aria-label="Business card back">
    <div class="back-brand">
      <span class="back-brand__mark"></span>
      <span class="back-brand__name">HARWICK PARTNERS</span>
    </div>
  </section>
</main>
</body>
</html>
```